Business Card Design for Software Development Company

I am looking for a business card design the incorporates my new logo (attached below).

Key information to include:
Name: Martin Quelbrook
Title: CEO
Email: martin@brightwellcivic.example
Phone: 555-218-9403
Website: www.brightwellcivic.example

NOTE: This design should be easy to edit so that we can order cards for different members of our team.

```html
<!DOCTYPE html>
<html lang="en">
<head>
<meta charset="utf-8">
<title>Brightwell Labs — Business Card</title>
<link href="https://fonts.googleapis.com/css2?family=Montserrat:wght@500;700&family=Jost:wght@400;500&display=swap" rel="stylesheet">
<style>
  :root {
    --backdrop: #e6e2dc;
    --card-light: #f4f4f4;
    --card-light-edge: #e7e7e7;
    --navy: #2f3852;
    --navy-deep: #283049;
    --orange: #e07b24;
    --teal: #1f9e8b;
    --ink-light: #ffffff;
    --ink-soft: #dfe3ec;
    --tint-mint: rgba(190, 228, 226, 0.45);
    --tint-blush: rgba(248, 214, 210, 0.45);
    --tint-slate: rgba(70, 92, 110, 0.35);
    --tint-plum: rgba(80, 60, 80, 0.35);
  }
  * { box-sizing: border-box; margin: 0; padding: 0; }
  html, body {
    width: 1200px; height: 900px; overflow: hidden;
    background: var(--backdrop);
  }
  .canvas {
    position: relative; width: 1200px; height: 900px;
    display: flex; flex-direction: column; align-items: center;
    justify-content: center; gap: 40px;
  }
  .card {
    position: relative; width: 700px; height: 400px; overflow: hidden;
    box-shadow: 0 10px 24px rgba(0, 0, 0, 0.18);
  }
  .card--front {
    border-radius: 40px 40px 40px 0;
    background:
      linear-gradient(160deg, var(--tint-mint) 0%, transparent 38%),
      linear-gradient(200deg, var(--tint-blush) 0%, transparent 45%),
      linear-gradient(120deg, var(--card-light-edge) 0%, var(--card-light) 60%);
  }
  .card--back {
    border-radius: 0 40px 0 40px;
    background:
      linear-gradient(160deg, var(--tint-slate) 0%, transparent 40%),
      linear-gradient(200deg, var(--tint-plum) 0%, transparent 45%),
      var(--navy);
  }
  .brand {
    position: absolute; display: flex; flex-direction: column; align-items: flex-end;
  }
  .brand__row { display: flex; align-items: center; gap: 14px; }
  .brand__dot {
    width: 30px; height: 30px; border-radius: 50%; background: var(--orange);
  }
  .brand__name {
    font-family: "Montserrat", sans-serif; font-weight: 700;
    font-size: 58px; letter-spacing: -1px; line-height: 1;
  }
  .brand__tagline {
    font-family: "Montserrat", sans-serif; font-weight: 500;
    font-size: 10px; letter-spacing: 0.6px; text-transform: uppercase; margin-top: 6px;
  }
  .card--front .brand { left: 120px; top: 165px; }
  .card--front .brand__name,
  .card--front .brand__tagline { color: var(--navy); }
  .card--back .brand { right: 48px; bottom: 60px; }
  .card--back .brand__name { font-size: 44px; color: var(--ink-light); }
  .card--back .brand__dot { width: 24px; height: 24px; }
  .card--back .brand__tagline { color: var(--ink-light); font-size: 8px; }
  .person { position: absolute; left: 60px; top: 72px; }
  .person__name {
    font-family: "Montserrat", sans-serif; font-weight: 700;
    font-size: 24px; letter-spacing: 0.5px; text-transform: uppercase; color: var(--orange);
  }
  .person__title {
    font-family: "Jost", sans-serif; font-weight: 400; font-size: 22px;
    color: var(--ink-soft); margin-top: 2px;
  }
  .contact { list-style: none; margin-top: 30px; }
  .contact__item {
    display: flex; align-items: center; gap: 12px; margin-bottom: 10px;
    font-family: "Jost", sans-serif; font-size: 19px; color: var(--ink-light);
  }
  .contact__icon { width: 20px; height: 20px; flex: none; }
</style>
</head>
<body>
<main class="canvas">
  <section class="card card--front" aria-label="Card front">
    <div class="brand">
      <div class="brand__row">
        <span class="brand__dot"></span>
        <span class="brand__name">Brightwell Labs</span>
      </div>
      <span class="brand__tagline">A division of Brightwell Civic</span>
    </div>
  </section>

  <section class="card card--back" aria-label="Card back">
    <div class="person">
      <h1 class="person__name">Martin Quelbrook</h1>
      <p class="person__title">CEO</p>
      <ul class="contact">
        <li class="contact__item">
          <svg class="contact__icon" viewBox="0 0 24 24" aria-hidden="true"><path fill="var(--teal)" d="M6.6 10.8a15.1 15.1 0 0 0 6.6 6.6l2.2-2.2a1 1 0 0 1 1-.25 11.4 11.4 0 0 0 3.6.57 1 1 0 0 1 1 1V20a1 1 0 0 1-1 1A17 17 0 0 1 3 4a1 1 0 0 1 1-1h3.5a1 1 0 0 1 1 1c0 1.25.2 2.45.57 3.6a1 1 0 0 1-.25 1z"/></svg>
          <span>555-218-9403</span>
        </li>
        <li class="contact__item">
          <svg class="contact__icon" viewBox="0 0 24 24" aria-hidden="true"><rect x="2" y="5" width="20" height="14" rx="1.5" fill="var(--teal)"/><path d="M3 6.5l9 6.5 9-6.5" fill="none" stroke="var(--navy)" stroke-width="1.6"/></svg>
          <span>martin@brightwellcivic.example</span>
        </li>
        <li class="contact__item">
          <svg class="contact__icon" viewBox="0 0 24 24" aria-hidden="true"><g fill="none" stroke="var(--teal)" stroke-width="1.6"><circle cx="12" cy="12" r="9"/><ellipse cx="12" cy="12" rx="4" ry="9"/><path d="M3 12h18M4.5 7.5h15M4.5 16.5h15"/></g></svg>
          <span>www.brightwellcivic.example</span>
        </li>
      </ul>
    </div>
    <div class="brand">
      <div class="brand__row">
        <span class="brand__dot"></span>
        <span class="brand__name">Brightwell Labs</span>
      </div>
      <span class="brand__tagline">A division of Brightwell Civic</span>
    </div>
  </section>
</main>
</body>
</html>
```